Brightarc Orthodontics appointment card design

I need appointment cards/ business cards made. Front will be Logo, name, title, email, phone number and location (5263 Walnut Hollow Pkwy, Ste 412, Concord, NC 28027) . the back should have an appointment card (name, time, date) and also 3 addresses listed with a check box so we can check to which location they are going.
Dale Fenwick Orthodontics
- 6735 Orchard Street, Ste 514, Harrisburg, NC 28075
- 3647 Ridgeway Drive NE, Ste 810, Concord, NC 28025
- 2917 Thornbury Corporate Drive, Ste 605, Charlotte, NC 28277
Business card can be horizontal or vertical in Design.
I need to be able to edit it to update and add new employees

Requirements
Must have
• Front:
• - Logo
• - Name & Title (able to be edited)
• - phone (704-555-0186) & Email (need to be able to edit)
• - Address: 5263 Walnut Hollow Pkwy, Ste 412
• Concord, NC 28027
• Back:
• Appointment Card design:
• - Name, time, Date
• - 3 locations w/ a check box so the patient knows where to go:
• Dale Fenwick Orthodontics
• - 6735 Orchard Street, Ste 514, Harrisburg, NC 28075
• - 3647 Ridgeway Drive NE, Ste 810, Concord, NC 28025
• - 2917 Thornbury Corporate Drive, Ste 605, Charlotte, NC 28277

```html
<!DOCTYPE html>
<html lang="en">
<head>
<meta charset="utf-8">
<title>Brightarc Orthodontics – Appointment &amp; Business Card</title>
<link rel="stylesheet" href="https://fonts.googleapis.com/css2?family=Roboto:wght@400;500;700&display=swap">
<style>
  :root {
    --bg: #3a3a3c;
    --card: #ffffff;
    --brand-blue: #1a73be;
    --ink: #4a4a4a;
    --rule: #333333;
  }
  * { box-sizing: border-box; margin: 0; padding: 0; }
  html, body { width: 1200px; height: 1000px; overflow: hidden; }
  body {
    background: var(--bg);
    font-family: "Roboto", Arial, sans-serif;
    color: var(--ink);
    position: relative;
  }
  .card {
    position: absolute;
    left: 220px;
    width: 760px;
    height: 434px;
    background: var(--card);
    border-radius: 28px;
    overflow: hidden;
  }
  .card--appointment { top: 50px; }
  .card--contact { top: 516px; }

  /* Appointment side */
  .top-band { position: absolute; left: 0; top: 0; width: 100%; height: 16px; background: var(--brand-blue); }
  .appt-title { position: absolute; left: 40px; top: 52px; font-size: 21px; font-weight: 700; color: var(--brand-blue); }
  .brand-name { font-weight: 700; color: var(--brand-blue); line-height: 1.05; }
  .card--appointment .brand-name { position: absolute; right: 40px; top: 60px; font-size: 30px; text-align: right; }
  .field { position: absolute; display: flex; align-items: flex-end; font-size: 15px; }
  .field .line { flex: 1; border-bottom: 1.5px solid var(--rule); margin-left: 10px; height: 1px; }
  .field--name { left: 40px; top: 108px; width: 430px; }
  .field--date { left: 40px; top: 148px; width: 430px; }
  .field--time { left: 40px; top: 198px; width: 680px; }
  .ampm { position: absolute; top: 228px; display: flex; align-items: center; gap: 6px; font-size: 15px; }
  .ampm--am { left: 560px; }
  .ampm--pm { left: 640px; }
  .checkbox { width: 15px; height: 15px; border: 2px solid var(--brand-blue); display: inline-block; }
  .practice-name { position: absolute; left: 0; width: 100%; top: 262px; text-align: center; font-size: 15px; }
  .practice-name strong { color: var(--brand-blue); font-size: 21px; font-weight: 700; }
  .locations { position: absolute; left: 30px; right: 30px; top: 306px; display: flex; justify-content: space-between; }
  .location { width: 220px; text-align: center; font-size: 13px; line-height: 1.35; }
  .location .checkbox { margin-bottom: 8px; }

  /* Contact side */
  .person-name { position: absolute; left: 46px; top: 44px; font-size: 21px; font-weight: 700; color: var(--brand-blue); letter-spacing: 0.3px; }
  .person-title { position: absolute; left: 46px; top: 72px; font-size: 15px; }
  .contact-list { position: absolute; left: 46px; top: 104px; font-size: 15px; line-height: 1.4; list-style: none; }
  .contact-list li { display: flex; align-items: center; gap: 8px; }
  .contact-list .address { display: block; margin-bottom: 6px; }
  .icon { width: 13px; height: 13px; fill: var(--brand-blue); flex: none; }
  .card--contact .brand-name { position: absolute; left: 46px; top: 262px; font-size: 52px; }
</style>
</head>
<body>

<section class="card card--appointment" aria-label="Appointment card">
  <div class="top-band"></div>
  <h2 class="appt-title">Next Appointment</h2>
  <div class="brand-name">Brightarc<br>Orthodontics</div>

  <div class="field field--name"><span>Name</span><span class="line"></span></div>
  <div class="field field--date"><span>Date</span><span class="line"></span></div>
  <div class="field field--time"><span class="line" style="margin-left:0;margin-right:10px"></span><span>Time</span><span class="line"></span></div>
  <div class="ampm ampm--am"><span class="checkbox"></span>AM</div>
  <div class="ampm ampm--pm"><span class="checkbox"></span>PM</div>

  <p class="practice-name"><strong>Dale Fenwick</strong> Orthodontics</p>

  <div class="locations">
    <div class="location"><span class="checkbox"></span><br>6735 Orchard Street, Ste 514,<br>Harrisburg, NC 28075</div>
    <div class="location"><span class="checkbox"></span><br>3647 Ridgeway Drive NE, Ste 810,<br>Concord, NC 28025</div>
    <div class="location"><span class="checkbox"></span><br>2917 Thornbury Corporate Drive,<br>Ste 605, Charlotte, NC 28277</div>
  </div>
</section>

<section class="card card--contact" aria-label="Business card">
  <h1 class="person-name">DALE FENWICK</h1>
  <p class="person-title">Orthodontics</p>
  <ul class="contact-list">
    <li class="address">5263 Walnut Hollow Pkwy,<br>Ste 412 - Concord, NC 28027</li>
    <li>
      <svg class="icon" viewBox="0 0 24 24" aria-hidden="true"><path d="M6.6 10.8a15.1 15.1 0 0 0 6.6 6.6l2.2-2.2c.3-.3.7-.4 1-.2 1.1.4 2.3.6 3.6.6.6 0 1 .4 1 1V20c0 .6-.4 1-1 1A17 17 0 0 1 3 4c0-.6.4-1 1-1h3.5c.6 0 1 .4 1 1 0 1.3.2 2.5.6 3.6.1.3 0 .7-.2 1z"/></svg>
      704-555-0186
    </li>
    <li>
      <svg class="icon" viewBox="0 0 24 24" aria-hidden="true"><path d="M2 5h20v14H2z M3.5 6.5 12 13l8.5-6.5" fill="none" stroke="#1a73be" stroke-width="2.4"/></svg>
      dalefenwick@brightarcmail.com
    </li>
  </ul>
  <div class="brand-name">Brightarc<br>Orthodontics</div>
</section>

</body>
</html>
```